New website design and logo for FlintBoro.com to help ignite the website sales.

Hi designers,

Flintboro is a new welding brand that is selling welding equipement.

Currently I have around 5 to 10 products. The issue is that the site itself does not do that much of sales. So I have to do something about the seo etc. but that is out of scope for the design.

What is in scope is to comeup with a new logo and website look and feel that is in line with the customers.

men, non professionals, garage, home improvements, perhaps sme ( small mediul entreprice business that want to start in the welding industry.

Products are midrange prices and quality. The look and feel must breath cool stuff, sexy ( women in working cloths carrying welding gloves, other protection gear and weldels)

The wedsite is build in wordpress with the Kora theme. I am an IT guy myself withhout any creativity in me :( so if you can help me with that that would be great.

Please have a quick look at flintboro.com

Best regards,
Joris

Target Market(s)

non professional welders that do metal work in there garage

Coding

Coded - Design and coding required

Number of Pages Required

3 page

Font styles to use
Sans Serif

Colors
0355a3
ffc214

Requirements
Must have
• I would like to see a new homepage and product page design together with a new logo.
Nice to have
• shop design

```html
<!DOCTYPE html>
<html lang="en">
<head>
<meta charset="utf-8">
<title>FlintBoro – Welding Equipment</title>
<link rel="stylesheet" href="https://fonts.googleapis.com/css2?family=Montserrat:ital,wght@0,500;0,600;0,700;1,500&family=Arimo:wght@400;700&display=swap">
<style>
:root{
  --blue:#0b5bc6;
  --blue-dark:#0a4fae;
  --orange:#fca716;
  --ink:#2b2b2b;
  --muted:#6b6b6b;
  --line:#e4e4e4;
  --white:#ffffff;
  --photo-bg:#f3f3f3;
}
*{box-sizing:border-box;margin:0;padding:0}
html,body{width:1200px;height:3344px;overflow:hidden;background:var(--white)}
body{position:relative;font-family:'Arimo',Arial,sans-serif;color:var(--ink)}

/* header */
.site-header{position:absolute;left:0;top:0;width:1200px;height:165px}
.brand{position:absolute;display:flex;align-items:center;gap:10px;z-index:3}
.site-header .brand{left:112px;top:22px;height:60px}
.brand-mark{width:34px;height:34px;border-radius:50%;background:var(--orange);flex:none}
.brand-name{font-family:'Montserrat',sans-serif;font-weight:700;font-size:28px;color:var(--blue)}
.icon-btn{position:absolute;top:17px;width:63px;height:63px;border-radius:50%;display:flex;align-items:center;justify-content:center}
.icon-btn.search{left:953px;background:var(--blue)}
.icon-btn.cart{left:1026px;background:var(--orange)}
.main-nav{position:absolute;left:0;top:99px;width:1200px;height:63px;background:var(--blue);border-bottom:3px solid var(--white);box-shadow:0 3px 0 var(--blue)}
.main-nav a{position:absolute;top:0;height:63px;line-height:63px;font-family:'Montserrat',sans-serif;font-weight:600;font-size:15px;color:var(--white);text-decoration:none;transform:translateX(-50%);white-space:nowrap}
.main-nav a.active{background:var(--orange);width:125px;text-align:center}

/* hero */
.hero{position:absolute;left:0;top:165px;width:1200px;height:686px;
  background:
  radial-gradient(ellipse 150px 120px at 720px 420px,#ffd28a 0%,#f09a3a 25%,rgba(200,110,40,0) 75%),
  radial-gradient(ellipse 420px 320px at 720px 430px,rgba(190,105,45,.85) 0%,rgba(110,60,35,.5) 40%,rgba(20,30,50,0) 75%),
  radial-gradient(ellipse 230px 250px at 760px 170px,#2a5ca8 0%,#163766 45%,rgba(10,18,32,0) 80%),
  radial-gradient(ellipse 300px 380px at 980px 300px,#1e3f72 0%,rgba(10,18,32,0) 75%),
  linear-gradient(90deg,#0a1322 0%,#111b2c 45%,#152238 75%,#0d1524 100%)}
.hero h1{position:absolute;left:110px;top:190px;font-family:'Montserrat',sans-serif;font-weight:600;font-size:55px;color:var(--white)}
.hero p{position:absolute;left:110px;top:270px;width:420px;font-family:'Montserrat',sans-serif;font-style:italic;font-weight:500;font-size:26px;line-height:42px;color:var(--white)}
.btn{display:inline-block;font-family:'Montserrat',sans-serif;font-weight:500;text-align:center;border-radius:40px;text-decoration:none}
.hero .btn{position:absolute;left:110px;top:422px;width:171px;height:57px;line-height:57px;background:var(--orange);color:var(--white);font-size:17px}

/* headings */
.section-title{position:absolute;left:0;width:1200px;text-align:center;font-family:'Montserrat',sans-serif;font-weight:600;font-size:35px;color:var(--blue)}
.title-rule{position:absolute;left:574px;width:52px;height:3px;background:var(--orange)}

/* products */
.product-card{position:absolute;width:237px;height:391px;background:var(--white);box-shadow:0 0 5px rgba(0,0,0,.18);text-align:center}
.product-media{position:absolute;left:7px;top:7px;width:223px;height:226px;background-color:var(--photo-bg)}
.product-name{position:absolute;left:0;top:254px;width:237px;font-family:'Montserrat',sans-serif;font-weight:500;font-size:19px;color:var(--ink);white-space:nowrap}
.product-price{position:absolute;left:0;top:290px;width:237px;font-family:'Montserrat',sans-serif;font-weight:500;font-size:16px;color:var(--blue)}
.product-price s{color:var(--muted);margin-right:4px}
.product-card .btn{position:absolute;left:53px;top:327px;width:131px;height:44px;line-height:40px;border:2px solid var(--orange);color:var(--orange);font-size:12px;font-weight:600}
.product-card .btn.filled{background:var(--blue);border-color:var(--blue);color:var(--white)}

.media-red-welder{background:radial-gradient(ellipse 62px 72px at 112px 118px,#c9302c 0%,#a82622 55%,rgba(243,243,243,0) 100%),var(--photo-bg)}
.media-blue-welder{background:radial-gradient(ellipse 72px 62px at 148px 110px,#2f6fc4 0%,#245ba8 55%,rgba(243,243,243,0) 100%),radial-gradient(ellipse 52px 62px at 72px 112px,#b8bcc2 0%,#9a9ea5 55%,rgba(243,243,243,0) 100%),var(--photo-bg)}
.media-helmet{background:radial-gradient(ellipse 22px 26px at 100px 105px,#9a4fd8 0%,#7b3dbb 60%,rgba(30,30,30,0) 100%),radial-gradient(ellipse 62px 82px at 112px 112px,#2a2a2c 0%,#1c1c1e 60%,rgba(243,243,243,0) 100%),var(--photo-bg)}
.media-gloves{background:radial-gradient(ellipse 42px 48px at 150px 58px,#3a3fc8 0%,#2d31a8 60%,rgba(243,243,243,0) 100%),radial-gradient(ellipse 70px 52px at 112px 130px,#e2a73c 0%,#c98a22 55%,rgba(243,243,243,0) 100%),var(--photo-bg)}
.media-kit{background:radial-gradient(ellipse 38px 36px at 156px 100px,#d8302a 0%,#b8231f 55%,rgba(243,243,243,0) 100%),radial-gradient(ellipse 58px 48px at 70px 110px,#3a3030 0%,#2a2222 55%,rgba(243,243,243,0) 100%),var(--photo-bg)}
.media-cable{background:radial-gradient(ellipse 96px 36px at 112px 108px,#2a2a2a 0%,#1a1a1a 50%,rgba(243,243,243,0) 100%),var(--photo-bg)}
.media-square{background:radial-gradient(ellipse 66px 70px at 118px 112px,#3b3026 0%,#2a2119 55%,rgba(243,243,243,0) 100%),var(--photo-bg)}

/* about */
.about{position:absolute;left:0;top:1896px;width:1200px;height:451px}
.about-photo{position:absolute;left:0;top:0;width:1200px;height:451px;background:
  radial-gradient(ellipse 90px 80px at 970px 300px,#e6f0ff 0%,#8fb4e8 35%,rgba(70,110,170,0) 80%),
  radial-gradient(ellipse 260px 230px at 900px 240px,rgba(80,110,160,.75) 0%,rgba(50,60,80,.4) 45%,rgba(40,40,50,0) 80%),
  linear-gradient(90deg,#4a3f36 0%,#2e2b2b 55%,#3d342c 100%)}
.about-shape{position:absolute;left:0;top:0}
.about h2{position:absolute;left:112px;top:50px;font-family:'Montserrat',sans-serif;font-weight:600;font-size:30px;color:var(--white)}
.about .rule{position:absolute;left:112px;top:100px;width:54px;height:3px;background:var(--white)}
.about p{position:absolute;left:112px;top:124px;width:440px;font-size:13.5px;line-height:25.8px;color:var(--white);text-align:justify}
.about .btn{position:absolute;left:112px;top:357px;width:158px;height:53px;line-height:53px;background:var(--blue);color:var(--white);font-size:17px}

/* blog */
.blog-card{position:absolute;top:2482px;width:312px}
.blog-media{width:312px;height:234px}
.blog-date{margin-top:22px;font-family:'Montserrat',sans-serif;font-weight:500;font-size:18px;color:var(--orange)}
.blog-title{margin-top:11px;font-family:'Montserrat',sans-serif;font-weight:500;font-size:17px;line-height:26px;color:var(--ink)}
.blog-text{margin-top:12px;font-size:13.5px;line-height:26px;color:var(--muted)}

/* footer */
.site-footer{position:absolute;left:0;top:2954px;width:1200px;height:390px;background:var(--blue);color:var(--white)}
.site-footer .brand{left:168px;top:88px}
.site-footer .brand-name{color:var(--white)}
.pay-badges{position:absolute;left:147px;top:218px;display:flex;gap:4px}
.pay-badges span{width:42px;height:30px;background:var(--white);border-radius:3px}
.footer-col{position:absolute;top:64px}
.footer-col h3{font-family:'Montserrat',sans-serif;font-weight:600;font-size:22px;margin-bottom:22px}
.footer-links{list-style:none}
.footer-links li{font-size:15.5px;line-height:30px;display:flex;align-items:center;gap:18px}
.footer-links li::before{content:"»";font-size:15px;margin-left:4px}
.contact-list{font-size:13.5px;line-height:21px}
.contact-list p{margin-bottom:10px}
.newsletter p{font-size:13.5px;line-height:24px;width:225px}
.email-input{margin-top:17px;width:225px;height:42px;background:var(--white);border-radius:4px;color:var(--ink);font-size:14px;line-height:42px;padding-left:14px}
.newsletter .btn{margin-top:10px;width:99px;height:40px;line-height:40px;background:var(--orange);color:var(--white);font-size:13px;font-weight:600}
.footer-rule{position:absolute;left:112px;top:316px;width:976px;height:1px;background:rgba(255,255,255,.25)}
.copyright{position:absolute;left:0;top:342px;width:1200px;text-align:center;font-size:15.5px}
</style>
</head>
<body>

<header class="site-header">
  <div class="brand"><span class="brand-mark"></span><span class="brand-name">FlintBoro</span></div>
  <a class="icon-btn search" aria-label="Search">
    <svg width="18" height="18" viewBox="0 0 18 18"><circle cx="7.5" cy="7.5" r="5.5" fill="none" stroke="#fff" stroke-width="2.4"/><line x1="11.5" y1="11.5" x2="16" y2="16" stroke="#fff" stroke-width="2.6" stroke-linecap="round"/></svg>
  </a>
  <a class="icon-btn cart" aria-label="Cart">
    <svg width="20" height="18" viewBox="0 0 20 18"><path d="M1 2h3l2.2 9h10l2-6.5H6" fill="none" stroke="#fff" stroke-width="2.2" stroke-linejoin="round"/><circle cx="8" cy="15" r="1.8" fill="#fff"/><circle cx="15" cy="15" r="1.8" fill="#fff"/></svg>
  </a>
  <nav class="main-nav">
    <a class="active" style="left:349px">HOME</a>
    <a style="left:491px">PRODUCTS</a>
    <a style="left:666px">WINKELMAND</a>
    <a style="left:857px">MIJN ACCOUNT</a>
    <a style="left:1041px">CONTACT US</a>
  </nav>
</header>

<section class="hero" role="img" aria-label="Welder in a helmet working on steel with bright sparks">
  <h1>FlintBoro</h1>
  <p>Simple welding of steel and aluminum Get great results with tools that work</p>
  <a class="btn">READ MORE</a>
</section>

<h2 class="section-title" style="top:900px">OUR PRODUCTS</h2>
<div class="title-rule" style="top:955px"></div>

<article class="product-card" style="left:110px;top:1003px">
  <div class="product-media media-red-welder" role="img" aria-label="Red MIG welding machine"></div>
  <h3 class="product-name">MIG-250P</h3>
  <div class="product-price"><s>€ 845.00</s> € 795.00</div>
  <a class="btn">ADD TO CART</a>
</article>
<article class="product-card" style="left:358px;top:1003px">
  <div class="product-media media-blue-welder" role="img" aria-label="Blue and grey MIG welding machine"></div>
  <h3 class="product-name">MIG-2500</h3>
  <div class="product-price"><s>€ 845.00</s> € 795.00</div>
  <a class="btn filled">ADD TO CART</a>
</article>
<article class="product-card" style="left:606px;top:1003px">
  <div class="product-media media-helmet" role="img" aria-label="Black welding helmet with purple visor"></div>
  <h3 class="product-name">Welding Helmet 180º</h3>
  <div class="product-price"><s>€ 845.00</s> € 795.00</div>
  <a class="btn">ADD TO CART</a>
</article>
<article class="product-card" style="left:854px;top:1003px">
  <div class="product-media media-gloves" role="img" aria-label="Blue and yellow leather welding gloves"></div>
  <h3 class="product-name">Welding gloves Blue</h3>
  <div class="product-price"><s>€ 845.00</s> € 795.00</div>
  <a class="btn">ADD TO CART</a>
</article>

<article class="product-card" style="left:110px;top:1431px">
  <div class="product-media media-helmet" role="img" aria-label="Large black welding helmet"></div>
  <h3 class="product-name">Welding Helmet Large</h3>
  <div class="product-price"><s>€ 845.00</s> € 795.00</div>
  <a class="btn">ADD TO CART</a>
</article>
<article class="product-card" style="left:358px;top:1431px">
  <div class="product-media media-kit" role="img" aria-label="Welding kit with machine, helmet and red gloves"></div>
  <h3 class="product-name">Product Name</h3>
  <div class="product-price"><s>€ 845.00</s> € 795.00</div>
  <a class="btn">ADD TO CART</a>
</article>
<article class="product-card" style="left:606px;top:1431px">
  <div class="product-media media-cable" role="img" aria-label="Welding cable with electrode holder"></div>
  <h3 class="product-name">Product Name</h3>
  <div class="product-price"><s>€ 845.00</s> € 795.00</div>
  <a class="btn">ADD TO CART</a>
</article>
<article class="product-card" style="left:854px;top:1431px">
  <div class="product-media media-square" role="img" aria-label="Black triangular steel square"></div>
  <h3 class="product-name">Kleine meetdriehoek</h3>
  <div class="product-price"><s>€ 845.00</s> € 795.00</div>
  <a class="btn">ADD TO CART</a>
</article>

<section class="about">
  <div class="about-photo" role="img" aria-label="Welder working on a steel beam in a workshop with sparks"></div>
  <svg class="about-shape" width="1200" height="451" viewBox="0 0 1200 451">
    <polygon points="0,0 578,0 714,451 0,451" fill="#ffffff"/>
    <polygon points="0,0 570,0 706,451 0,451" fill="#fca716"/>
  </svg>
  <h2>ABOUT OUR FLINTBORO</h2>
  <div class="rule"></div>
  <p>Sed ut perspiciatis unde omnis iste natus error sit voluptatem accu santium doloremque laudantium, totam rem aperiam, eaque ipsa quae ab illo inventore veritatis et quasi architecto beatae vitae dicta sunt explicabo. Nemo enim ipsam voluptatem quia voluptas sit aspernatur aut odit aut fugit, sed quia consequuntur magni dolores eos qui ratione voluptatem sequi nesciunt.Neque porro quisquam est, qui dolorem ipsum quia dolor sit amet, consectetur, adipisci velit, sed quia non numquam labore et dolore magnam aliquam quaerat voluptatem.</p>
  <a class="btn">READ MORE</a>
</section>

<h2 class="section-title" style="top:2397px">LATEST BLOG</h2>
<div class="title-rule" style="top:2451px"></div>

<article class="blog-card" style="left:112px">
  <div class="blog-media" role="img" aria-label="Gloved hands welding with sparks" style="background:radial-gradient(ellipse 50px 40px at 240px 150px,#ffd59a,rgba(230,130,50,0) 80%),radial-gradient(ellipse 140px 100px at 230px 150px,#c86a2a,rgba(40,45,60,0) 80%),linear-gradient(135deg,#2e3548,#1b2130)"></div>
  <div class="blog-date">05 July 2021</div>
  <h3 class="blog-title">Sed ut perspiciatis unde omnis iste na tus error sit volupta</h3>
  <p class="blog-text">Nemo enim ipsam voluptatem quia voluptas sit as pernatur aut odit aut fugit, sed quia consequu ratio ne voluptatem sequi nesciunt.</p>
</article>
<article class="blog-card" style="left:444px">
  <div class="blog-media" role="img" aria-label="Welder in a dark workshop with a shower of sparks" style="background:radial-gradient(ellipse 60px 40px at 110px 200px,#ffcf8a,rgba(230,130,50,0) 80%),radial-gradient(ellipse 160px 90px at 150px 195px,#c97a36,rgba(30,35,45,0) 80%),linear-gradient(180deg,#424a58,#1f232c)"></div>
  <div class="blog-date">05 July 2021</div>
  <h3 class="blog-title">Sed ut perspiciatis unde omnis iste na tus error sit volupta</h3>
  <p class="blog-text">Nemo enim ipsam voluptatem quia voluptas sit as pernatur aut odit aut fugit, sed quia consequu ratio ne voluptatem sequi nesciunt.</p>
</article>
<article class="blog-card" style="left:776px">
  <div class="blog-media" role="img" aria-label="Welder crouching at a construction site" style="background:radial-gradient(ellipse 40px 30px at 210px 200px,#eef4ff,rgba(180,200,230,0) 80%),radial-gradient(ellipse 90px 110px at 120px 130px,#5a4a3a,rgba(90,95,100,0) 80%),linear-gradient(180deg,#9aa5b2,#5b5a55)"></div>
  <div class="blog-date">05 July 2021</div>
  <h3 class="blog-title">Sed ut perspiciatis unde omnis iste na tus error sit volupta</h3>
  <p class="blog-text">Nemo enim ipsam voluptatem quia voluptas sit as pernatur aut odit aut fugit, sed quia consequu ratio ne voluptatem sequi nesciunt.</p>
</article>

<footer class="site-footer">
  <div class="brand"><span class="brand-mark"></span><span class="brand-name">FlintBoro</span></div>
  <div class="pay-badges" aria-label="Accepted payment methods"><span></span><span></span><span></span><span></span><span></span></div>

  <div class="footer-col" style="left:452px">
    <h3>LINKS</h3>
    <ul class="footer-links">
      <li>Home</li><li>products</li><li>shopping cart</li><li>My account</li><li>Contact Us</li>
    </ul>
  </div>
  <div class="footer-col" style="left:642px">
    <h3>GET IN TOUCH</h3>
    <div class="contact-list">
      <p style="margin-top:10px">Tele : 000.123.1231</p>
      <p>2050 Lorem Ipsum Dummy<br>Lorem CA 95110</p>
      <p>info@flintboro.com</p>
    </div>
  </div>
  <div class="footer-col newsletter" style="left:862px">
    <h3>NEWSLETTER</h3>
    <p>Sed ut perspiciatis unde error sit vol uptatem accusantium...</p>
    <div class="email-input">Enter Email Id :</div>
    <a class="btn">SUBMIT</a>
  </div>
  <div class="footer-rule"></div>
  <div class="copyright">© Copyright 2021.FlintBoro.All Rights Reserved</div>
</footer>

</body>
</html>
```